Clear Plastic Card Design

I am looking to have a business card designed from my logo icon. I am looking to match the style of a different business card I have attached in the files.
Looking for a card that is plastic, with layers of transparency in the shape of my logo icon (also attached in the files) - not a circle like the other card. The winning design will incorporate the red icon logo on the front and back and include the charity's name, "Light for the Weary Souls" in the same or similar font, as well as an email and phone number. For now, use the email: email@lightfortheweary-mail.org and the phone number 555-382-7194.
We like how the sample business card has transparency, partial and full opacity layers and a matching color scheme. Files will need to be in vector so that our business card printing company can work with it.
UPDATE:
We've some excellent designs in, thank you everyone! I got an early review from the owner, and he requested a minor redirect to find his perfect design. He wants the design to stand out by NOT being a rectangle. Try instead a circle, square, or best yet - something that falls in the outline of the logo icon, either fully or partially. Thank you, everyone!
Light for the Weary Souls text should be incorporated as well as a phone and email.

```html
<!DOCTYPE html>
<html lang="en">
<head>
<meta charset="utf-8">
<title>Light for the Weary Souls – Clear Card</title>
<link href="https://fonts.googleapis.com/css2?family=Questrial&family=Roboto+Condensed:wght@400&display=swap" rel="stylesheet">
<style>
  :root {
    --backdrop: #d9cfc0;
    --card-fill: rgba(255, 255, 255, 0.38);
    --card-edge: #b9b3ab;
    --brand-red: #9e1b1b;
    --ink: #2a2422;
    --rule: #5a5350;
  }
  html, body {
    margin: 0;
    padding: 0;
    width: 1200px;
    height: 969px;
    overflow: hidden;
    background: var(--backdrop);
  }
  .canvas {
    position: relative;
    width: 1200px;
    height: 969px;
  }
  .card-shape {
    position: absolute;
    left: 0;
    top: 0;
  }
  .brand {
    position: absolute;
    left: 420px;
    top: 330px;
    width: 400px;
    text-align: center;
  }
  .brand-dot {
    display: block;
    width: 74px;
    height: 74px;
    margin: 0 auto 18px;
    border-radius: 50%;
    background: var(--brand-red);
  }
  .brand-name {
    margin: 0;
    font-family: "Questrial", sans-serif;
    font-weight: 400;
    font-size: 27px;
    line-height: 1.08;
    color: var(--ink);
  }
  .contact-list {
    position: absolute;
    left: 420px;
    top: 570px;
    width: 400px;
    margin: 0;
    padding: 0;
    list-style: none;
    text-align: center;
    font-family: "Roboto Condensed", sans-serif;
    font-size: 24px;
    line-height: 28px;
    color: var(--ink);
  }
</style>
</head>
<body>
<main class="canvas">
  <svg class="card-shape" width="1200" height="969" viewBox="0 0 1200 969" aria-hidden="true">
    <circle class="card-body" cx="620" cy="494" r="262" fill="var(--card-fill)" stroke="var(--card-edge)" stroke-width="2"/>
    <circle class="card-ring" cx="620" cy="494" r="244" fill="none" stroke="var(--brand-red)" stroke-width="3"/>
    <g class="contact-divider" stroke="var(--rule)" stroke-width="1.2">
      <line x1="428" y1="537" x2="546" y2="537"/>
      <line x1="696" y1="537" x2="808" y2="537"/>
    </g>
    <g class="contact-icons" fill="var(--brand-red)">
      <path class="icon-phone" d="M558 524c2-2 5-2 6 0l4 6c1 2 0 4-2 5l-2 1c1 4 5 8 9 10l1-2c1-2 3-3 5-2l6 4c2 1 2 4 0 6l-3 3c-3 2-9 1-16-5s-11-14-10-19z"/>
      <g class="icon-mail">
        <rect x="606" y="530" width="24" height="15" rx="1"/>
        <path d="M607 531l11 8 11-8" fill="none" stroke="#f2ece6" stroke-width="1.5"/>
      </g>
      <g class="icon-globe">
        <circle cx="668" cy="536" r="12"/>
        <path d="M662 530c3-2 6 0 5 3s-4 2-4 5 2 4 1 6M671 527c-1 3 1 5 4 5s3 4 1 6" fill="none" stroke="#f2ece6" stroke-width="1.6"/>
      </g>
    </g>
  </svg>

  <div class="brand">
    <span class="brand-dot"></span>
    <h1 class="brand-name">Light for the<br>Weary Souls</h1>
  </div>

  <ul class="contact-list">
    <li class="contact-phone">555-382-7194</li>
    <li class="contact-email">email@lightfortheweary-mail.org</li>
    <li class="contact-web">www.lightfortheweary-souls.org</li>
  </ul>
</main>
</body>
</html>
```